Website Design for Forklift Training Company

DO NOT CONTACT PRIVATELY. ONLY SUBMISSIONS HERE WILL BE CONSIDERED

I need a design for a website that offers forklift training courses.

The company offers accredited, onsite forklift training that are customized for the needs of each individual company. The company offers a variety of courses to operate forklifts and other machinary.

About: "KVW Training Ltd delivers bespoke onsite forklift truck operator training throught the uk.
All our instructors have a wealth of knowledge and expertise to provide your company with all your forklift truck training requirements.
KVW Training Ltd is registered and accredited by plomvex standards so you can be rest assured that all forklift training is carried out the very highest standard"

I need the following pages designed:
> a) Home Page: Include a header image, ways to contact, about snippet, overview of courses, accreditation that will be received after completing the courses. (See attachments for samples)
> b) About Page
> c) Contact Us Page
> d) Course Page Template: A page that will be used as template for the courses offered. It should contain;
1. Cover image for the course
2. A description of the course
3. A table indicating the various course options
4. Course Objectives
5. What the trainee will receive after doing the course (example: a certification)

Industrial Businesses

4 page

Colors
0054AA
0677BA
7BADD7
CADEEF
E8F1F8
0094D4
00A9DD
6FCCEA
C7EBF8
E9F6FB

• - No Search bar

```html
<!DOCTYPE html>
<html lang="en">
<head>
<meta charset="utf-8">
<title>KVW Training Ltd – Forklift Truck Operator Training</title>
<link href="https://fonts.googleapis.com/css2?family=Montserrat:wght@800&family=Roboto+Condensed:wght@400;700&family=Roboto:wght@400;500;700&display=swap" rel="stylesheet">
<style>
:root{
  --navy:#0054AA;
  --blue:#0677BA;
  --sky:#7BADD7;
  --pale:#CADEEF;
  --mist:#E8F1F8;
  --cyan:#0094D4;
  --bright:#00A9DD;
  --aqua:#6FCCEA;
  --ice:#C7EBF8;
  --frost:#E9F6FB;
  --charcoal:#2b3440;
  --text:#555b63;
}
html,body{margin:0;padding:0;width:1200px;height:4552px;overflow:hidden;background:#fff}
*{box-sizing:border-box}
.page{position:relative;width:1200px;height:4552px;overflow:hidden;font-family:"Roboto",Arial,sans-serif;color:var(--text)}
.abs{position:absolute}

/* header */
.site-header{position:absolute;left:0;top:0;width:1200px;height:76px;background:#fff;box-shadow:0 2px 8px rgba(0,0,0,.12);z-index:5}
.brand{position:absolute;left:120px;top:19px;font-family:"Roboto Condensed",sans-serif;font-weight:700;font-size:28px;color:var(--cyan);letter-spacing:.3px}
.nav-link{position:absolute;top:27px;font-family:"Roboto Condensed",sans-serif;font-size:15px;color:#3d4550;letter-spacing:.3px}
.nav-link.active{color:var(--cyan)}
.nav-bar{position:absolute;left:442px;top:71px;width:46px;height:5px;background:var(--cyan)}
.phone{position:absolute;left:980px;top:25px;font-family:"Roboto Condensed",sans-serif;font-weight:700;font-size:16px;color:var(--navy);display:flex;align-items:center;gap:6px}

/* hero */
.hero{position:absolute;left:0;top:76px;width:1200px;height:702px;background:linear-gradient(90deg,#0b3f86 0%,#1d4f8f 35%,#6d7f95 55%,#a3a9b0 75%,#c7c6bd 100%)}
.hero-photo{position:absolute;left:520px;top:76px;width:680px;height:600px;background:radial-gradient(ellipse at 40% 45%,rgba(230,210,60,.55) 0%,rgba(200,190,90,.25) 30%,rgba(0,0,0,0) 60%),linear-gradient(180deg,#9aa3ad 0%,#8c8f92 60%,#b84a1f 100%);opacity:.85}
.hero-shade{position:absolute;left:0;top:76px;width:800px;height:600px;background:linear-gradient(90deg,rgba(8,52,120,.96) 0%,rgba(8,52,120,.85) 45%,rgba(8,52,120,0) 100%)}
.hero-kicker{position:absolute;left:113px;top:250px;font-family:"Roboto",sans-serif;font-size:23px;color:#fff;letter-spacing:.3px}
.hero-title{position:absolute;left:113px;top:286px;font-family:"Montserrat",sans-serif;font-weight:800;font-size:45px;line-height:44px;color:#fff;margin:0}
.btn{position:absolute;display:flex;align-items:center;justify-content:center;font-family:"Roboto Condensed",sans-serif;font-weight:700;font-size:14px;letter-spacing:2.5px}
.btn-hero{left:120px;top:433px;width:164px;height:40px;background:var(--cyan);color:#fff;box-shadow:4px 4px 0 #fff}
.dot{position:absolute;top:680px;width:12px;height:12px;border-radius:50%;background:#fff}
.dot.on{background:var(--cyan)}

/* about */
.about-ring{position:absolute;border-radius:50%;border:1px solid var(--sky)}
.about-photo{position:absolute;border-radius:50%}
.section-title{position:absolute;margin:0;font-family:"Roboto Condensed",sans-serif;font-weight:700;color:var(--navy)}
.section-title .hl{color:var(--cyan)}
.about-copy{position:absolute;left:657px;width:428px;font-size:14px;line-height:23.5px;color:var(--text);margin:0}
.btn-solid{background:var(--cyan);color:#fff;box-shadow:-4px 4px 0 var(--navy)}

/* courses */
.kicker{position:absolute;left:0;width:1200px;text-align:center;font-family:"Roboto Condensed",sans-serif;font-size:15px;letter-spacing:3px;color:var(--navy)}
.card{position:absolute;padding:0}
.card-title{position:absolute;margin:0;font-family:"Roboto Condensed",sans-serif;font-weight:700;font-size:23px;color:#fff}
.ticks{position:absolute;margin:0;padding:0;list-style:none;font-size:11.5px;line-height:20px;color:#fff}
.ticks li{position:relative;padding-left:24px;white-space:nowrap}
.ticks li::before{content:"";position:absolute;left:0;top:4px;width:13px;height:13px;border-radius:50%;background:#fff}
.ticks li::after{content:"";position:absolute;left:4px;top:6px;width:3px;height:6px;border:solid var(--navy);border-width:0 2px 2px 0;transform:rotate(45deg)}
.ticks.on-cyan li::after{border-color:var(--cyan)}
.ticks.on-dark li::after{border-color:var(--charcoal)}
.btn-light{background:#fff;color:var(--navy);box-shadow:-4px 4px 0 var(--navy);font-size:12px}
.btn-light.dark{color:var(--charcoal);box-shadow:-4px 4px 0 #1a2129}
.photo{position:absolute}
.icon-badge{position:absolute;width:70px;height:70px;border-radius:50%;background:#fff;border:3px solid var(--pale);box-shadow:0 0 0 3px rgba(255,255,255,.6);display:flex;align-items:center;justify-content:center}

/* accreditation */
.acc-card{position:absolute;top:3264px;width:479px;height:408px;background:#fff;box-shadow:0 4px 18px rgba(0,40,90,.12)}
.acc-text{position:absolute;left:50px;top:173px;width:379px;margin:0;text-align:center;font-size:12px;line-height:21.5px;color:var(--text)}

/* contact */
.contact-band{position:absolute;left:0;top:3778px;width:1200px;height:590px;background:linear-gradient(135deg,#0a4fa3 0%,#0b5cb5 50%,#0a4c9c 100%)}
.contact-panel{position:absolute;left:168px;top:3855px;width:401px;height:465px;background:linear-gradient(160deg,var(--bright) 0%,var(--cyan) 55%,var(--blue) 100%)}
.contact-kicker{position:absolute;right:744px;top:3906px;font-family:"Roboto Condensed",sans-serif;font-weight:700;font-size:19px;color:#fff;text-align:right}
.contact-title{position:absolute;right:744px;top:3936px;margin:0;text-align:right;font-family:"Roboto Condensed",sans-serif;font-weight:700;font-size:36px;line-height:42px;color:#fff}
.form-card{position:absolute;left:486px;top:3900px;width:562px;height:390px;background:#fff;box-shadow:0 6px 24px rgba(0,0,0,.2)}
.form-title{position:absolute;left:48px;top:36px;margin:0;font-family:"Roboto",sans-serif;font-weight:500;font-size:23px;color:#1d232b}
.field{position:absolute;width:205px}
.field .label{font-size:13px;font-weight:700;color:#1d232b}
.field .value{margin-top:10px;font-size:10.5px;color:#8a9099;padding-bottom:9px;border-bottom:1px solid #cfd4da}
.send{position:absolute;left:451px;top:292px;width:57px;height:57px;border-radius:50%;background:var(--navy);display:flex;align-items:center;justify-content:center}
.to-top{position:absolute;left:585px;top:4343px;width:50px;height:50px;border-radius:50%;background:var(--cyan);border:3px solid #fff;display:flex;align-items:center;justify-content:center;z-index:2}

/* footer */
.foot-link{position:absolute;top:4422px;font-family:"Roboto Condensed",sans-serif;font-size:17px;color:var(--navy)}
.copyright{position:absolute;left:0;top:4460px;width:1200px;text-align:center;font-size:11.5px;color:var(--blue)}
.social{position:absolute;top:4499px;width:20px;height:20px;border-radius:50%;background:var(--navy)}
</style>
</head>
<body>
<div class="page">

  <!-- header -->
  <header class="site-header">
    <div class="brand">KVW TRAINING LTD</div>
    <span class="nav-link active" style="left:445px">HOME</span>
    <span class="nav-link" style="left:548px">ABOUT US</span>
    <span class="nav-link" style="left:678px">OUR COURSES</span>
    <span class="nav-link" style="left:836px">CONTACT US</span>
    <div class="nav-bar"></div>
    <div class="phone">
      <svg width="18" height="18" viewBox="0 0 24 24" fill="none" stroke="#0054AA" stroke-width="2"><path d="M22 16.9v3a2 2 0 0 1-2.2 2 19.8 19.8 0 0 1-8.6-3.1 19.5 19.5 0 0 1-6-6A19.8 19.8 0 0 1 2.1 4.2 2 2 0 0 1 4.1 2h3a2 2 0 0 1 2 1.7c.1.9.4 1.8.7 2.7a2 2 0 0 1-.5 2.1L8 9.8a16 16 0 0 0 6 6l1.3-1.3a2 2 0 0 1 2.1-.4c.9.3 1.8.6 2.7.7a2 2 0 0 1 1.7 2z"/></svg>
      (555) 010-4821
    </div>
  </header>

  <!-- hero -->
  <section class="hero"></section>
  <div class="hero-photo" role="img" aria-label="Instructor and trainee operating a forklift truck in a warehouse"></div>
  <div class="hero-shade"></div>
  <div class="hero-kicker">KVW TRAINING LTD</div>
  <h1 class="hero-title">FORKLIFT TRUCK<br>OPERATOR<br>TRAINING</h1>
  <div class="btn btn-hero">CONTACT US</div>
  <svg class="abs" style="left:0;top:600px" width="1200" height="190" viewBox="0 600 1200 190">
    <polygon points="0,640 600,763 1200,672 1200,790 0,790" fill="#fff"/>
    <polygon points="150,668 600,762 1060,688 1060,693 600,782 150,672" fill="#0094D4"/>
    <polyline points="130,664 600,760 1080,684" fill="none" stroke="#7BADD7" stroke-width="1"/>
  </svg>
  <div class="dot" style="left:568px"></div>
  <div class="dot" style="left:595px"></div>
  <div class="dot on" style="left:623px"></div>

  <!-- about -->
  <div class="about-ring" style="left:142px;top:811px;width:452px;height:452px"></div>
  <div class="about-ring" style="left:152px;top:818px;width:440px;height:440px;border-color:var(--pale)"></div>
  <div class="about-photo" role="img" aria-label="Smiling trainee seated on a forklift truck" style="left:167px;top:842px;width:402px;height:402px;background:radial-gradient(circle at 60% 40%,#e9e6df 0%,#b8bcc2 45%,#4a5058 100%)"></div>
  <div class="about-photo" role="img" aria-label="Operator in a hard hat at the forklift controls" style="left:371px;top:1060px;width:212px;height:212px;border:6px solid #fff;background:radial-gradient(circle at 50% 45%,#f1d64a 0%,#c9b24a 35%,#3d4f6a 100%)"></div>
  <h2 class="section-title" style="left:657px;top:875px;font-size:36px"><span class="hl">ABOUT</span> KVW TRAINING LTD</h2>
  <p class="about-copy" style="top:943px">KVW Training Ltd delivers bespoke onsite forklift truck operator training throught the uk. All our instructors have a wealth of knowledge and expertise to provide your company with all your forklift truck training requirements.</p>
  <p class="about-copy" style="top:1060px">KVW Training Ltd is registered and accredited by plomvex standards so you can be rest assured that all forklift training is carried out the very highest standard</p>
  <div class="btn btn-solid" style="left:665px;top:1161px;width:164px;height:40px">LEARN MORE</div>

  <!-- courses background -->
  <svg class="abs" style="left:0;top:1300px" width="1200" height="1820" viewBox="0 1300 1200 1820">
    <defs>
      <linearGradient id="courseFade" x1="0" y1="0" x2="0" y2="1">
        <stop offset="0" stop-color="#E8F1F8"/>
        <stop offset="0.75" stop-color="#F3F8FC"/>
        <stop offset="1" stop-color="#ffffff"/>
      </linearGradient>
    </defs>
    <polygon points="0,1435 600,1316 1200,1435 1200,3120 0,3120" fill="url(#courseFade)"/>
    <polygon points="0,1435 600,1316 1200,1435 1200,1437 600,1326 0,1438" fill="#0054AA"/>
    <path d="M465,1908 V1950 Q465,1975 490,1975 H712 Q737,1975 737,2000 V2020" fill="none" stroke="#7BADD7" stroke-width="1.5"/>
    <circle cx="737" cy="2029" r="8" fill="#fff" stroke="#0677BA" stroke-width="3"/>
    <path d="M737,2467 V2520 Q737,2545 712,2545 H490 Q465,2545 465,2570" fill="none" stroke="#7BADD7" stroke-width="1.5"/>
    <circle cx="465" cy="2578" r="8" fill="#fff" stroke="#0677BA" stroke-width="3"/>
    <path d="M336,3011 V3060 Q336,3085 361,3085 H579 Q604,3085 604,3110 V3120" fill="none" stroke="#7BADD7" stroke-width="1.5"/>
  </svg>
  <svg class="abs" style="left:594px;top:3118px" width="20" height="20" viewBox="0 0 20 20"><circle cx="10" cy="10" r="7" fill="#fff" stroke="#0677BA" stroke-width="3"/></svg>

  <div class="kicker" style="top:1382px">WHAT WE OFFER</div>
  <h2 class="section-title" style="left:0;width:1200px;text-align:center;top:1402px;font-size:40px"><span class="hl">OUR</span> COURSES</h2>

  <!-- forklift training -->
  <div class="photo" role="img" aria-label="Two engineers in hard hats inspecting a forklift" style="left:546px;top:1497px;width:572px;height:424px;background:linear-gradient(120deg,#7a5a3a 0%,#c9b86a 30%,#e0cf4a 50%,#8f949a 75%,#5e646b 100%)"></div>
  <div class="abs" style="left:102px;top:1523px;width:180px;height:370px;background:var(--bright)"></div>
  <div class="card" style="left:110px;top:1534px;width:554px;height:350px;background:var(--navy)"></div>
  <h3 class="card-title" style="left:155px;top:1570px">FORKLIFT TRAINING</h3>
  <ul class="ticks" style="left:157px;top:1614px">
    <li>Bendro Truck Training Course</li>
    <li>Cambra Lift Training course</li>
    <li>Counterbalance Training Course</li>
    <li>Flexor Truck Training Course</li>
    <li>Harlo Crane Training Course</li>
    <li>Llop Training Course</li>
    <li>Marrow Truck Training Course</li>
    <li>Order Picker Truck Training Course</li>
    <li>Pedestrian Training Course</li>
  </ul>
  <ul class="ticks" style="left:391px;top:1614px">
    <li>Pivot Steer Training Course</li>
    <li>Reach Training Course</li>
    <li>Rough Terrain Training Course</li>
    <li>Sideloader Training Course</li>
    <li>Telescopic Handeler Training Course</li>
    <li>Tow Tractor Training Course</li>
    <li>Vna Man Down Truck Training Course</li>
    <li>Vna Man Up Truck Training Course</li>
  </ul>
  <div class="btn btn-light" style="left:157px;top:1815px;width:136px;height:35px">LEARN MORE</div>
  <div class="icon-badge" style="left:631px;top:1665px">
    <svg width="36" height="36" viewBox="0 0 36 36" fill="none" stroke="#0054AA" stroke-width="2"><rect x="6" y="12" width="14" height="12"/><path d="M10 12V6h8l2 6M24 4v24M24 28h8"/><circle cx="10" cy="28" r="3"/><circle cx="19" cy="28" r="3"/></svg>
  </div>

  <!-- MEWP training -->
  <div class="photo" role="img" aria-label="Boom lifts with orange platforms raised against the sky" style="left:85px;top:2044px;width:586px;height:423px;background:linear-gradient(160deg,#2f82c9 0%,#7bb3de 45%,#c9dbe8 70%,#d48b3c 100%)"></div>
  <div class="abs" style="left:936px;top:2071px;width:177px;height:367px;background:var(--navy)"></div>
  <div class="card" style="left:574px;top:2085px;width:527px;height:346px;background:var(--cyan)"></div>
  <h3 class="card-title" style="left:645px;top:2158px">MEWP TRAINING</h3>
  <ul class="ticks on-cyan" style="left:647px;top:2202px">
    <li>Cherry Picker Training Course</li>
    <li>Scissor Lift Training Course</li>
    <li>Harness And Lanyard Training Course</li>
  </ul>
  <div class="btn btn-light" style="left:651px;top:2288px;width:132px;height:35px">LEARN MORE</div>
  <div class="icon-badge" style="left:537px;top:2200px">
    <svg width="34" height="34" viewBox="0 0 34 34" fill="none" stroke="#0094D4" stroke-width="2"><rect x="7" y="4" width="20" height="7"/><path d="M10 11l14 8M24 11L10 19M10 19l14 8M24 19L10 27"/><rect x="6" y="27" width="22" height="4"/></svg>
  </div>

  <!-- other training -->
  <div class="photo" role="img" aria-label="Worker giving a thumbs up beside a blue truck and a traffic cone" style="left:542px;top:2588px;width:576px;height:423px;background:linear-gradient(100deg,#2b3f9e 0%,#3350c2 40%,#8fa0b8 65%,#c8cdd2 100%)"></div>
  <div class="abs" style="left:104px;top:2617px;width:180px;height:368px;background:var(--bright)"></div>
  <div class="card" style="left:115px;top:2627px;width:491px;height:349px;background:var(--charcoal)"></div>
  <h3 class="card-title" style="left:189px;top:2678px;font-size:26px">OTHER TRAINING</h3>
  <ul class="ticks on-dark" style="left:191px;top:2725px">
    <li>Bolder Truck Training &nbsp;Course</li>
    <li>Front Loading Shovel TrainingCourse</li>
    <li>Overhead &nbsp;Pendant Crane Training Course</li>
    <li>Swing Colum Jib Crane Training Course</li>
    <li>Slingingand Signalling Training Course</li>
    <li>Vehicle Banksman &nbsp;Training Course</li>
  </ul>
  <div class="btn btn-light dark" style="left:193px;top:2875px;width:134px;height:35px">LEARN MORE</div>
  <div class="icon-badge" style="left:566px;top:2757px">
    <svg width="34" height="34" viewBox="0 0 34 34" fill="none" stroke="#2b3440" stroke-width="2"><circle cx="17" cy="15" r="9"/><path d="M17 10v6M17 19v1M11 26l-3 5M23 26l3 5"/></svg>
  </div>

  <!-- accreditation -->
  <div class="kicker" style="top:3162px;font-size:15px">FORKLIFT CERTIFICATE</div>
  <h2 class="section-title" style="left:0;width:1200px;text-align:center;top:3184px;font-size:32px">FORKLIFT TRAINING <span class="hl">ACCREDITATION</span></h2>

  <div class="abs" style="left:118px;top:3257px;width:160px;height:160px;background:var(--cyan)"></div>
  <div class="acc-card" style="left:125px">
    <div class="abs" role="img" aria-label="Accreditation badge" style="left:193px;top:33px;width:101px;height:92px;background:#2a2f7a;box-shadow:inset 0 -24px 0 #34399a"></div>
    <p class="acc-text">PLOMVEX is recognised throughout the united kingdom and Ireland as one of the leading material handling equipment training accrediting bodies. PLOMVEX is a founder member of the TOLVA (trade board of lift and vehicle assessors) and this replaced the accrediting bodies forum previously run by the Varden safety forum. They have over 40 years experience of setting training standards,accreditation and monitoring. The PLOMVEX accreditation schemes are supported by legal requirements for training.</p>
  </div>

  <div class="abs" style="left:950px;top:3520px;width:160px;height:160px;background:var(--navy)"></div>
  <div class="acc-card" style="left:625px">
    <div class="abs" role="img" aria-label="Workplace transport accreditation badge" style="left:188px;top:46px;width:104px;height:58px;border-radius:8px;background:#2f4f5f"></div>
    <p class="acc-text">We are accredited by the PLOMVEX who are recognised by the national Varden safety office as competent to deliver forklift truck operator training courses. As an PLOMVEX accredited training provider we are monitored annually to ensure we are maintaining our high standards as laid down by the PLOMVEX. All our instructors are qualified and registered with the PLOMVEX and monitored. Please note we are only accredited to deliver training at customer premises as we do not have a training centre.</p>
  </div>

  <!-- contact -->
  <section class="contact-band" role="img" aria-label="Warehouse interior in deep blue tones"></section>
  <div class="contact-panel"></div>
  <div class="contact-kicker">CONTACT US</div>
  <h2 class="contact-title">LET'S GET<br>START TRAINING</h2>
  <div class="photo" role="img" aria-label="Yellow counterbalance forklift truck" style="left:159px;top:4055px;width:247px;height:239px;background:radial-gradient(ellipse at 50% 55%,#f2c230 0%,#d9a21f 35%,rgba(40,40,40,.6) 65%,rgba(0,0,0,0) 75%)"></div>

  <div class="form-card">
    <h3 class="form-title">Send Us A Message</h3>
    <div class="field" style="left:51px;top:104px"><div class="label">Your Name</div><div class="value">Alex Reed</div></div>
    <div class="field" style="left:299px;top:104px"><div class="label">Company</div><div class="value">Lorem ipsum dolor sit amet</div></div>
    <div class="field" style="left:51px;top:187px"><div class="label">Email Address</div><div class="value">alex.reed@example.com</div></div>
    <div class="field" style="left:299px;top:187px"><div class="label">Phone</div><div class="value">01122-123-456-789</div></div>
    <div class="field" style="left:51px;top:272px;width:390px"><div class="label">Message</div><div class="value">Hi, do you have a moment to talk abo...|</div></div>
    <div class="send">
      <svg width="22" height="22" viewBox="0 0 24 24" fill="#fff"><path d="M22 2L2 10l7 3 3 7z"/><path d="M22 2L9 13" stroke="#0054AA" stroke-width="1.5"/></svg>
    </div>
  </div>

  <div class="to-top">
    <svg width="20" height="20" viewBox="0 0 20 20" fill="none" stroke="#fff" stroke-width="2"><path d="M10 17V4M4 10l6-6 6 6"/></svg>
  </div>

  <!-- footer -->
  <footer>
    <span class="foot-link" style="left:355px">HOME</span>
    <span class="foot-link" style="left:478px">ABOUT US</span>
    <span class="foot-link" style="left:630px">COURSES</span>
    <span class="foot-link" style="left:777px">CONTACT US</span>
    <div class="copyright">2021 © Copyright Company All Right Reserved</div>
    <span class="social" style="left:581px"></span>
    <span class="social" style="left:608px"></span>
    <span class="social" style="left:636px"></span>
  </footer>
</div>
</body>
</html>
```